Im want a website LIKE VRX's and FleetHollow.com's with product payment options like Trenzo's

I need a website LIKE VRX with a header made EXACTLY LIKE THAT OF FLEETHOLLOWS .

The front page photo should be like that of FLEETHOLLOW's webpage as well.

The name of the website will be called "M.K. (Caldera Key)".

We will be targeting ALL MARKETS in a small town in central Panama and charging businesses "listing fees" like a phone book does but also providing informational blogs, news, and other interesting activities.

THIS IS A MULTI PAGE WEBSITE

THIS IS WHERE VRX's website meets Brivelle/FleetHollow.

Once the layout is built I will tweak and modify, add information, and upload items for sale.

Here is a list of specific categories that should be listed out above the front page header image/search bar

-- Home -- News -- Travel -- Activities -- Shop & Dine -- Store -- More... --

These categories should be spread across the bottom of the page in three sections:

WHATS SO GREAT ABOUT (Caldera Key),
HAND PICKED TOURS
ACTIVITIES etc.

Also lets use www.Trenzo.example 's
"HOT DESTINATIONS"
"BEAT THE BEST PRICES IN BOQUETE"
"OCTOBERS INSIDER PICKS"
"TOP DESTINATIONS"
and spread them in four sections side-by-side near the bottom of the page.

Overall I would like to see the finished product to be something LIKE VRX's and FleetHollows.

WE NEED ONLINE PAYMENT OPTIONS LIKE BRIVELLE'S WEBSITE HAS

This will be a desktop website but should be very mobile friendly as well.

-rodmund

P.S. Good luck!

If it isn't already too late to change the website name, the name of the website should be "Caldera Key". Added Friday, October 9, 2015

What do you guys think the budget should be to win this? Added Saturday, October 10, 2015

www.palmorra.example is the most amazing simple site. Whoever can make me a replica with my specifications will win immediately!!!! Added Sunday, October 18, 2015

OMG www.palmorra.example is the bomb!So simple and elegant. Whoever can make me an EXACT REPLICA OF WWW.PALMORRA.EXAMPLE as my site with the specifications mentioned in my brief will take home the $825.00 immediately! Good luck amigos! Added Sunday, October 18, 2015

Does anybody know how to add recurring monthly billing options on this website? Added Sunday, October 18, 2015

ALL MARKETS

Product

Coded - Design and coding required

5+ page

• Coinvey payment options.
• I must be able to add and remove photos/text and video from the HTML files in the page.
• Be creative my friends, and may the odds be forever in your favor!
• I added some photos of a good layout for our page below.

```html
<!DOCTYPE html>
<html lang="en">
<head>
<meta charset="utf-8">
<title>Caldera Key</title>
<link href="https://fonts.googleapis.com/css2?family=Open+Sans:wght@400;600;700&family=Raleway:wght@500;600;700;800&display=swap" rel="stylesheet">
<style>
:root{
  --navy:#0a1d3b;
  --navy-2:#12305c;
  --blue:#1a4f93;
  --blue-bright:#2360ac;
  --red:#d0121b;
  --red-dark:#a80d14;
  --gray-band:#e6e7e9;
  --text:#4a4f57;
  --muted:#8a8f97;
  --line:#dadde2;
  --white:#ffffff;
  --footer:#111418;
  --star:#f2a71b;
}
*{box-sizing:border-box;margin:0;padding:0}
html,body{width:1200px;height:2432px;overflow:hidden}
body{font-family:"Open Sans",Arial,sans-serif;color:var(--text);background:var(--white);font-size:12px;position:relative}
h1,h2,h3,h4{font-family:"Raleway","Helvetica Neue",sans-serif}

/* header */
.site-header{height:128px;background:linear-gradient(180deg,var(--navy) 0%,var(--navy-2) 100%);position:relative;color:var(--white)}
.brand{position:absolute;left:40px;top:38px;display:flex;align-items:center;gap:12px}
.brand-mark{width:40px;height:40px;border-radius:50%;background:var(--white);opacity:.9}
.brand-name{font-family:"Raleway",sans-serif;font-weight:700;font-size:30px;letter-spacing:1px;color:var(--white)}
.account{position:absolute;right:40px;top:26px;font-size:11px;font-weight:600;letter-spacing:.5px}
.selectors{position:absolute;right:40px;top:58px;display:flex;gap:18px;font-size:12px;font-weight:600}
.selectors span{display:flex;align-items:center;gap:6px}
.selectors span::after{content:"";border:4px solid transparent;border-top-color:var(--white);margin-top:4px}

.main-nav{height:48px;background:var(--navy-2);border-top:1px solid rgba(255,255,255,.12);display:flex;align-items:center;padding:0 96px;position:relative}
.main-nav a{color:var(--white);text-decoration:none;font-size:11px;font-weight:700;letter-spacing:.5px;padding:0 20px;height:48px;line-height:48px}
.main-nav a.active{background:var(--red)}
.social{position:absolute;right:96px;top:13px;display:flex;gap:7px}
.social i{display:block;width:22px;height:22px;border-radius:50%;background:#c9ccd3}

/* hero */
.hero{height:604px;position:relative;background:linear-gradient(180deg,#3a1a10 0%,#b8421a 28%,#f29a2e 48%,#f7c55a 56%,#7a3a1c 70%,#241410 100%);color:var(--white)}
.hero-title{position:absolute;left:64px;top:224px;font-size:50px;font-weight:800;letter-spacing:1px}
.hero-text{position:absolute;left:64px;top:290px;width:560px;font-size:12px;line-height:18px;opacity:.9}
.hero-arrows{position:absolute;left:64px;top:340px;display:flex;gap:8px}
.hero-arrows i{width:20px;height:20px;border-radius:50%;background:rgba(255,255,255,.85);display:flex;align-items:center;justify-content:center}
.search-panel{position:absolute;left:112px;top:384px;width:976px;height:180px;background:rgba(255,255,255,.22);border:1px solid rgba(255,255,255,.35);padding:28px 32px}
.search-panel h2{font-size:26px;font-weight:600;letter-spacing:1px;margin-bottom:18px}
.search-row{display:flex;gap:16px}
.search-input{flex:0 0 600px;height:46px;background:var(--white);color:var(--muted);font-size:12px;line-height:46px;padding:0 16px}
.btn-red{background:var(--red);color:var(--white);font-weight:700;font-size:12px;letter-spacing:.5px;text-align:center}
.search-row .btn-red{flex:0 0 296px;height:46px;line-height:46px}

/* categories */
.categories{height:260px;background:var(--gray-band);display:flex;justify-content:center;gap:28px;padding-top:32px}
.category{width:304px;height:192px;background:linear-gradient(160deg,#2a3340,#0f141b);display:flex;align-items:center;justify-content:center;color:var(--white);font-family:"Raleway",sans-serif;font-weight:700;font-size:20px;letter-spacing:.5px}

/* packages */
.packages{width:976px;margin:0 auto;padding-top:40px;height:780px}
.section-head{display:flex;justify-content:space-between;align-items:flex-end;border-bottom:2px solid var(--line);padding-bottom:10px;margin-bottom:24px;position:relative}
.section-head h2{font-size:24px;font-weight:800;color:#2a2f37;letter-spacing:.3px}
.section-head::after{content:"";position:absolute;left:0;bottom:-2px;width:90px;height:2px;background:var(--red)}
.view-all{font-size:10px;font-weight:700;color:var(--red)}
.grid{display:grid;grid-template-columns:repeat(4,226px);gap:24px 24px}
.card{height:302px}
.card-photo{height:130px}
.p1{background:linear-gradient(180deg,#6fb8e2,#2c8fb8 60%,#1f6f6a)}
.p2{background:linear-gradient(180deg,#8fc9e4,#3e9ea9 60%,#20524a)}
.p3{background:linear-gradient(180deg,#5fb3e0,#1c8ec0 55%,#c7b68a)}
.p4{background:linear-gradient(180deg,#b7d9ef,#49a9d1 55%,#1b7f8f)}
.card p{font-size:11px;line-height:15px;margin:10px 0 6px}
.rating{display:flex;align-items:center;gap:6px;font-size:10px;color:var(--muted)}
.stars{color:var(--star);letter-spacing:1px;font-size:11px}
.meta{font-size:10px;color:var(--muted);margin-top:3px;display:flex;align-items:center;gap:5px}
.meta::before{content:"";width:7px;height:7px;border-radius:50%;background:var(--blue)}
.card-foot{display:flex;justify-content:space-between;align-items:flex-end;margin-top:14px}
.btn-details{background:var(--navy-2);color:var(--white);font-size:10px;font-weight:700;width:70px;height:26px;line-height:26px;text-align:center}
.price{text-align:right}
.price small{display:block;font-size:9px;color:var(--muted)}
.price b{font-size:22px;color:var(--red);font-weight:600;font-family:"Raleway",sans-serif}

/* info columns */
.info{width:976px;margin:0 auto;display:grid;grid-template-columns:260px 340px 328px;gap:24px;height:272px}
.info h3{font-size:15px;font-weight:800;color:#2a2f37;padding-bottom:8px;border-bottom:2px solid var(--line);margin-bottom:14px}
.faq li{list-style:none;display:flex;align-items:center;gap:8px;font-size:11px;margin-bottom:14px}
.faq li::before{content:"";width:12px;height:12px;border-radius:50%;background:var(--navy-2);flex:none}
.quote{border:1px solid var(--line);padding:14px 16px;font-size:11px;line-height:16px;color:var(--muted);font-style:italic;height:100px}
.author{display:flex;align-items:center;gap:12px;margin-top:10px}
.avatar{width:52px;height:52px;border-radius:50%;background:linear-gradient(135deg,#c7a58a,#5b4a40)}
.author b{font-size:11px;color:var(--red)}
.news-item{display:flex;gap:12px;margin-bottom:16px}
.date{flex:none;width:46px;height:40px;background:var(--navy-2);color:var(--white);font-size:10px;font-weight:700;text-align:center;line-height:40px}
.news-item p{font-size:11px;line-height:15px}

/* cta */
.cta{height:212px;background:linear-gradient(180deg,var(--blue-bright),var(--blue));color:var(--white);text-align:center;padding-top:34px}
.cta h2{font-size:20px;font-weight:700;letter-spacing:.3px}
.cta p{font-size:12px;line-height:18px;width:720px;margin:10px auto 20px;opacity:.9}
.cta .btn-red{display:inline-block;width:140px;height:40px;line-height:40px}

/* footer */
.site-footer{height:148px;background:var(--footer);color:#b9bdc4;display:grid;grid-template-columns:300px 200px 200px 200px;gap:24px;padding:28px 112px 0;font-size:10px;line-height:16px}
.site-footer h4{color:var(--white);font-size:12px;font-weight:700;margin-bottom:8px}
.foot-links{color:var(--white);font-weight:600}
.foot-social{display:flex;gap:6px;margin-top:10px}
.foot-social i{width:18px;height:18px;background:#3a3f47;display:block}
.ic{display:flex;align-items:center;gap:6px}
.ic::before{content:"";width:6px;height:6px;border-radius:50%;background:var(--red)}
</style>
</head>
<body>

<header class="site-header">
  <div class="brand"><span class="brand-mark"></span><span class="brand-name">CALDERA KEY</span></div>
  <div class="account">LOGIN &nbsp;|&nbsp; REGISTER</div>
  <div class="selectors"><span>EN</span><span>$</span></div>
</header>

<nav class="main-nav">
  <a class="active">HOME</a><a>TOURS</a><a>PACKAGES</a><a>HOTEL/HOSTELS</a><a>RENTAL VEHICLES</a><a>ABOUT US</a><a>CONTACT US</a>
  <div class="social"><i></i><i></i><i></i><i></i><i></i></div>
</nav>

<section class="hero" role="img" aria-label="Tropical beach at sunset with palm trees silhouetted against an orange sky">
  <h1 class="hero-title">CALDERA KEY</h1>
  <p class="hero-text">Lorem ipsum dolor sit amet, consectetur adipiscing elit, sed diam nonummy nibh euismod tincidunt ut laoreet dolore magna aliquam erat volutpat.</p>
  <div class="hero-arrows">
    <i><svg width="8" height="8" viewBox="0 0 8 8"><path d="M5.5 1 2.5 4l3 3" stroke="#0a1d3b" stroke-width="1.5" fill="none"/></svg></i>
    <i><svg width="8" height="8" viewBox="0 0 8 8"><path d="M2.5 1l3 3-3 3" stroke="#0a1d3b" stroke-width="1.5" fill="none"/></svg></i>
  </div>
  <div class="search-panel">
    <h2>SEARCH TOURS</h2>
    <div class="search-row"><div class="search-input">Search Keyword</div><div class="btn-red">FIND PACKAGES</div></div>
  </div>
</section>

<section class="categories">
  <div class="category" role="img" aria-label="Guided tour group photo">GUIDED TOURS</div>
  <div class="category" role="img" aria-label="Hotel room photo">HOTEL/HOSTELS</div>
  <div class="category" role="img" aria-label="Rental vehicle photo">RENTAL VEHICLES</div>
</section>

<section class="packages">
  <div class="section-head"><h2>LATEST TOUR PACKAGES</h2><span class="view-all">VIEW ALL</span></div>
  <div class="grid">
    <article class="card"><div class="card-photo p1" role="img" aria-label="Island lagoon with boats"></div><p>Lorem ipsum dolor sit amet, conse ctetur adipiscing elit</p><div class="rating"><span class="stars">★★★★★</span>138 Reviews</div><div class="meta">5 days tour, 4 nights</div><div class="card-foot"><div class="btn-details">DETAILS</div><div class="price"><small>From $90</small><b>$ 79.99</b></div></div></article>
    <article class="card"><div class="card-photo p2" role="img" aria-label="Limestone cliffs over turquoise sea"></div><p>Lorem ipsum dolor sit amet, conse ctetur adipiscing elit</p><div class="rating"><span class="stars">★★★★★</span>138 Reviews</div><div class="meta">5 days tour, 4 nights</div><div class="card-foot"><div class="btn-details">DETAILS</div><div class="price"><small>From $90</small><b>$ 79.99</b></div></div></article>
    <article class="card"><div class="card-photo p3" role="img" aria-label="Tropical beach with clear water"></div><p>Lorem ipsum dolor sit amet, conse ctetur adipiscing elit</p><div class="rating"><span class="stars">★★★★★</span>138 Reviews</div><div class="meta">5 days tour, 4 nights</div><div class="card-foot"><div class="btn-details">DETAILS</div><div class="price"><small>From $90</small><b>$ 79.99</b></div></div></article>
    <article class="card"><div class="card-photo p4" role="img" aria-label="Long-tail boat moored by a beach"></div><p>Lorem ipsum dolor sit amet, conse ctetur adipiscing elit</p><div class="rating"><span class="stars">★★★★★</span>138 Reviews</div><div class="meta">5 days tour, 4 nights</div><div class="card-foot"><div class="btn-details">DETAILS</div><div class="price"><small>From $90</small><b>$ 79.99</b></div></div></article>
    <article class="card"><div class="card-photo p2" role="img" aria-label="Boats on a calm bay"></div><p>Lorem ipsum dolor sit amet, conse ctetur adipiscing elit</p><div class="rating"><span class="stars">★★★★★</span>138 Reviews</div><div class="meta">5 days tour, 4 nights</div><div class="card-foot"><div class="btn-details">DETAILS</div><div class="price"><small>From $90</small><b>$ 79.99</b></div></div></article>
    <article class="card"><div class="card-photo p1" role="img" aria-label="Overwater resort bungalows"></div><p>Lorem ipsum dolor sit amet, conse ctetur adipiscing elit</p><div class="rating"><span class="stars">★★★★★</span>138 Reviews</div><div class="meta">5 days tour, 4 nights</div><div class="card-foot"><div class="btn-details">DETAILS</div><div class="price"><small>From $90</small><b>$ 79.99</b></div></div></article>
    <article class="card"><div class="card-photo p4" role="img" aria-label="Rocky island in the sea"></div><p>Lorem ipsum dolor sit amet, conse ctetur adipiscing elit</p><div class="rating"><span class="stars">★★★★★</span>138 Reviews</div><div class="meta">5 days tour, 4 nights</div><div class="card-foot"><div class="btn-details">DETAILS</div><div class="price"><small>From $90</small><b>$ 79.99</b></div></div></article>
    <article class="card"><div class="card-photo p3" role="img" aria-label="Palm tree over a sandy beach"></div><p>Lorem ipsum dolor sit amet, conse ctetur adipiscing elit</p><div class="rating"><span class="stars">★★★★★</span>138 Reviews</div><div class="meta">5 days tour, 4 nights</div><div class="card-foot"><div class="btn-details">DETAILS</div><div class="price"><small>From $90</small><b>$ 79.99</b></div></div></article>
  </div>
</section>

<section class="info">
  <div>
    <h3>FAQ</h3>
    <ul class="faq">
      <li>Lorem ipsum dolor sit amet, consectetur elit</li>
      <li>Sed diam nonummy nibh euismod</li>
      <li>Ut wisi enim ad minim veniam</li>
      <li>Duis autem vel eum iriure dolor</li>
    </ul>
  </div>
  <div>
    <h3>TESTIMONIALS</h3>
    <div class="quote">Lorem ipsum dolor sit amet, consectetur adipiscing elit, sed diam nonummy nibh euismod tincidunt ut laoreet dolore magna aliquam.</div>
    <div class="author"><div class="avatar" role="img" aria-label="Customer portrait"></div><b>ANA RUIZ</b></div>
  </div>
  <div>
    <h3>LATEST NEWS</h3>
    <div class="news-item"><div class="date">SEP 15</div><p>Lorem ipsum dolor sit amet, consectetur adipiscing elit sed diam nonummy.</p></div>
    <div class="news-item"><div class="date">SEP 12</div><p>Ut wisi enim ad minim veniam, quis nostrud exerci tation ullamcorper.</p></div>
  </div>
</section>

<section class="cta">
  <h2>QUISQUE EFFICITUR LIGULA AT JUSTO PORTTITOR, SED ALIQUET ARCU CONVALLIS</h2>
  <p>Lorem ipsum dolor sit amet, consectetur adipiscing elit. Sed eleifend efficitur scelerisque. In id bibendum eget nulla. Curabitur feugiat metus in tellus porta.</p>
  <div class="btn-red">GET A QUOTE</div>
</section>

<footer class="site-footer">
  <div>
    <div class="foot-links">Privacy Policy &nbsp;|&nbsp; Sitemap</div>
    <div>Copyright © 2015 Caldera Key. All Rights Reserved</div>
    <div class="foot-social"><i></i><i></i><i></i><i></i><i></i></div>
  </div>
  <div><h4>OUR LOCATION</h4><div>12 Calle Mirador, Plaza Sol</div><div>Central Panama</div></div>
  <div><h4>KEEP IN TOUCH</h4><div>Phone: +00 000 000 0000</div><div>Email: info@calderakey.example</div></div>
  <div><h4>QUICK LINKS</h4><div class="ic">Tours &amp; Packages</div><div class="ic">Hotel/Hostels</div><div class="ic">Rental Vehicles</div></div>
</footer>

</body>
</html>
```